IT consulting company looking for a modern business design for a website and a new logo

We are the IT-consulting company VelmaTrix from Germany and need a new and modern business website and a new logo. We are specialized in output management. Our services include business analysis, outsourcing, development, training and project leading. We wish for a design with nature pictures (mountains, lakes, rivers, forests, etc.) for our company with the colors green and blue. If it is possible, a slow-mo video of a nature scene. The design should be responsive and the menu should change to a hamburger menu. The following are: • Services / Solutions 1. Output Management 2. Outsourcing 3. Development 4. Business Analyst 5. Training • Partners • Careers • About Us 1. Project A 2. Project B 3. Project C • Contact Notes for the following categories: For "Services / Solutions" we want to conclude some contents from all the sub-points and sub-points below. Additionally, we would like to see some sub-point under "Services / Solutions". For Output Management: "5 Benefits of Output Management Systems (OMS) - OMS Simplifies and Accelerates External Communication - Helps Reduce Communication Mistakes - Provides Customers With Fast and Secure Responses to your questions - Employees can focus on the essential as they can access prepared templates - Companies get complete transparency about their communication "The point" partner does not have sub-points. The content here is a quote and the logo from the company Brel. For now, just placeholders on this site. The next point wants to be "career" without sub-point and wants to contain some text. Carrer options wants to be listed here. Next point wants to be "About us", where we need sub-points which we do not know exactly at this moment, but they will contain text. By clicking directly on "About us" we want to include pictures and texts about 6 employees for which we only need placeholders at the moment. The last point wants to be "contact", where customers can send us messages. The main page should include a story about our company, which can be a placeholder for now. For reference, designs have a look at: https://brelvanto.de/ https://www.tarnopix.com/ https://www.pldrive.de/ We prefer WordPress designs, created with the plugin ELEMENTOR, so that we can easily edit the content by ourselves. The final design should look professional, competent and modern.

Target Market(s)

With our website, we want to reach the following target groups. <br> <br> <br> <br> <br> <br> <br> <br> <br> <br> <br> <br> <br> <br> <br> <br> <br> <br> <br> <br> <br> <br> <br> <br> <br> <br> <br> <br> <br> <br> <br> <br> <br> <br> <br> <br> <br> <br> <br> <br> <br> <br> <br> <br> <br> <br> <br> <br> <br>

Industry/Entity Type

Consulting

Logo Text

(optionally) VelmaTrix

Font styles to use
Sans Serif

Colors

Designer to choose colors to be used in the design.

Requirements
Must have
• 1. Outsourcing 3. Development 4. Business Analyst 5. Training • Partners • Careers • About Us 1. Project A 2. Project B 3. Project C • Contact The above-mentioned background picture with nature motifs (mountains, lakes, rivers, forests, etc.). WordPress design in primary colors blue and green.
Nice to have
• ELEMENTOR template. Effects for the background pictures. Counter of all successful projects for Output Management, Business Analyst and Training

```html
<!DOCTYPE html>
<html lang="en">
<head>
<meta charset="utf-8">
<title>VelmaTrix – Output Management</title>
<link rel="stylesheet" href="https://fonts.googleapis.com/css2?family=Poppins:wght@400;500&family=Lato:ital,wght@0,400;0,700;1,400&display=swap">
<style>
:root{
  --green:#5aa52f;
  --green-dark:#4e9327;
  --ink:#222;
  --text:#555;
  --muted:#777;
  --line:#cfcfcf;
  --grey-bg:#f4f4f4;
  --hub:#e4e9df;
  --white:#fff;
}
*{box-sizing:border-box;margin:0;padding:0}
html,body{width:1200px;height:3777px;overflow:hidden}
body{position:relative;background:var(--white);font-family:"Lato",sans-serif;color:var(--text)}
.abs{position:absolute}
h1,h2,h3,h4,.nav,.brand{font-family:"Poppins",sans-serif;font-weight:400;color:var(--ink)}

/* header + hero */
.hero{left:0;top:0;width:1200px;height:650px;background:linear-gradient(180deg,#ffffff 0%,#fbf6ee 22%,#e9dcc4 34%,#5f7fae 46%,#2f4f8c 54%,#dfe7f2 66%,#ffffff 100%)}
.brand{left:110px;top:40px;font-size:32px;color:#333}
.nav{right:112px;top:50px;display:flex;gap:32px;font-size:15px;align-items:center}
.nav a{color:#333;text-decoration:none}
.nav a.active{color:var(--green)}
.nav .lang{font-size:13px;color:#666}
.hero-title{left:0;width:1200px;top:160px;text-align:center;font-size:50px;font-weight:500}
.hero-sub{left:0;width:1200px;top:244px;text-align:center;font-size:27px;color:#444}

/* welcome */
.section-title{left:0;width:1200px;text-align:center;font-size:50px;font-weight:500}
.welcome-text{left:210px;width:780px;top:900px;text-align:center;font-size:14.5px;line-height:30px;color:var(--muted)}
.video{left:368px;top:1040px;width:465px;height:293px;background:linear-gradient(135deg,#dfe6ee 0%,#b9c7d4 45%,#8f9aa4 70%,#d6d2cb 100%);box-shadow:0 10px 25px rgba(0,0,0,.2)}
.play{left:564px;top:1150px}

/* services */
.services{left:0;top:1448px;width:1200px;height:609px;background:var(--grey-bg);overflow:hidden}
.svc-label{font-family:"Poppins",sans-serif;font-size:21px;color:#333;line-height:31px}
.hub-name{left:0;width:1200px;top:1878px;text-align:center;font-family:"Poppins",sans-serif;font-weight:500;font-size:60px;color:var(--green)}

/* partners */
.card{width:311px;height:230px;border:1px solid var(--line);border-radius:3px;background:var(--white);text-align:center}
.card .mark{margin-top:44px;font-family:"Poppins",sans-serif;font-size:32px;font-weight:500;color:var(--green-dark)}
.card p{margin:30px 14px 0;font-style:italic;font-size:14px;line-height:26px;color:var(--muted)}

/* career */
.career{left:0;top:2596px;width:1200px;height:474px;background:linear-gradient(90deg,#6bb23f 0%,#5aa52f 60%,#62ab36 100%)}
.career h2{color:var(--white);font-size:52px}
.career-text{left:110px;top:2770px;width:400px;font-size:15px;line-height:29px;color:var(--white)}
.btn-more{left:110px;top:2924px;width:144px;height:46px;border-radius:23px;background:var(--white);color:#222;font:700 15px "Lato",sans-serif;display:flex;align-items:center;justify-content:center}
.job{width:243px;height:316px;background:var(--white)}
.job .pic{height:161px}
.job h4{font-size:18px;margin:24px 20px 0}
.job p{margin:8px 20px 0;font-size:14px;line-height:24px;color:var(--text)}
.job .go{position:absolute;right:16px;bottom:-13px}

/* contact */
.contact{left:0;top:3070px;width:1200px;height:707px;background:linear-gradient(180deg,#ffffff 0%,#f6f6f4 45%,#efe9e4 100%)}
.col-title{font-family:"Poppins",sans-serif;font-size:21px;color:#222}
.field{border:1px solid #bcbcbc;border-radius:4px;background:var(--white);font-size:13px;color:#666;padding:14px 15px}
.submit{left:608px;top:3582px;width:106px;height:40px;border-radius:20px;background:var(--green);color:var(--white);font:700 13px "Lato",sans-serif;display:flex;align-items:center;justify-content:center}
.info{left:778px;display:flex;gap:17px;align-items:flex-start;font-size:13.5px;line-height:24px;color:#555}
.ico{width:32px;height:32px;border-radius:50%;border:1px solid #bcbcbc;background:var(--white);display:flex;align-items:center;justify-content:center;flex:none}
.social{left:776px;top:3600px;display:flex;gap:14px}
.social span{width:33px;height:33px;border-radius:50%;border:1.5px solid var(--green);background:var(--white)}
.footer-line{left:110px;top:3676px;width:980px;height:1px;background:#cfcfcf}
.copyright{left:0;width:1200px;top:3716px;text-align:center;font-size:13.5px;color:#777}
</style>
</head>
<body>

<div class="abs hero" role="img" aria-label="Snowy mountain peaks rising above clouds at sunrise"></div>
<div class="abs brand">VelmaTrix</div>
<nav class="abs nav">
  <a class="active">Home</a><a>Services</a><a>Partner</a><a>Career</a><a>About us</a><a>Contact</a>
  <svg width="15" height="15" viewBox="0 0 15 15"><circle cx="6" cy="6" r="4.5" fill="none" stroke="#222" stroke-width="2"/><line x1="9.5" y1="9.5" x2="14" y2="14" stroke="#222" stroke-width="2.4"/></svg>
  <span class="lang">Eng &#9662;</span>
</nav>
<h1 class="abs hero-title">Specialised in Output Management</h1>
<p class="abs hero-sub">We are a IT consulting company in Germany</p>

<h2 class="abs section-title" style="top:808px">Welcome to VelmaTrix</h2>
<p class="abs welcome-text">Nam libero tempore, cum soluta nobis est eligendi optio cumque nihil impedit quo minus id quod maxime pla ceat facere possimus, omnis voluptas assumenda est, omnis dolor repellendus. Temporibus autem quibusdam et aut officiis debitis aut rerum necessitatibus saepe eveniet ut et voluptates repudiand</p>
<div class="abs video" role="img" aria-label="Video still: laptop showing charts on an office desk"></div>
<svg class="abs play" width="73" height="73" viewBox="0 0 73 73"><circle cx="36.5" cy="36.5" r="33" fill="#222" stroke="#5aa52f" stroke-width="4"/><path d="M29 23 L52 36.5 L29 50Z" fill="#fff"/></svg>

<div class="abs services">
  <svg class="abs" style="left:0;top:0" width="1200" height="609" viewBox="0 0 1200 609">
    <circle cx="600" cy="550" r="260" fill="#e4e9df"/>
    <circle cx="600" cy="550" r="281" fill="none" stroke="#5aa52f" stroke-width="2"/>
    <g fill="#fff" stroke="#5aa52f" stroke-width="2">
      <circle cx="600" cy="269" r="43"/>
      <circle cx="400" cy="336" r="43"/>
      <circle cx="791" cy="336" r="43"/>
      <circle cx="321" cy="517" r="43"/>
      <circle cx="877" cy="517" r="43"/>
    </g>
    <g fill="#222">
      <path d="M574 266 L600 256 L626 266 L600 276Z"/><path d="M586 271 V283 Q600 291 614 283 V271 L600 277Z"/><rect x="621" y="266" width="2" height="14"/>
      <circle cx="400" cy="336" r="17"/>
      <rect x="773" y="346" width="36" height="2.5"/><rect x="773" y="320" width="2.5" height="28"/><rect x="779" y="332" width="4" height="14"/><rect x="786" y="325" width="4" height="21"/><rect x="793" y="329" width="4" height="17"/><rect x="800" y="323" width="4" height="23"/>
      <path d="M309 496 H327 L336 505 V538 H309Z" fill="none" stroke="#222" stroke-width="2.5"/><circle cx="322" cy="520" r="6"/>
      <circle cx="870" cy="523" r="11"/><circle cx="888" cy="508" r="7"/><circle cx="888" cy="532" r="6"/>
    </g>
    <g fill="#fff"><path d="M392 326 Q400 330 397 338 Q406 342 404 350 Q396 346 392 338Z"/><circle cx="322" cy="520" r="2.5"/><circle cx="870" cy="523" r="4"/><circle cx="888" cy="508" r="2.5"/></g>
  </svg>
</div>
<h2 class="abs section-title" style="top:1518px">Our Services</h2>
<div class="abs svc-label" style="left:0;width:1200px;text-align:center;top:1618px">Training</div>
<div class="abs svc-label" style="left:204px;top:1777px">Outsourcing</div>
<div class="abs svc-label" style="left:861px;top:1768px">Business Analyst</div>
<div class="abs svc-label" style="left:108px;top:1927px;text-align:right;width:142px">Output Management</div>
<div class="abs svc-label" style="left:948px;top:1948px">Development</div>
<div class="abs hub-name">VelmaTrix</div>

<h2 class="abs section-title" style="top:2147px">Partners</h2>
<svg class="abs" style="left:44px;top:2360px" width="22" height="36" viewBox="0 0 22 36"><path d="M18 2 L4 18 L18 34" fill="none" stroke="#777" stroke-width="3"/></svg>
<svg class="abs" style="left:1136px;top:2360px" width="22" height="36" viewBox="0 0 22 36"><path d="M4 2 L18 18 L4 34" fill="none" stroke="#777" stroke-width="3"/></svg>
<div class="abs card" style="left:111px;top:2263px"><div class="mark">Orvenda</div><p>“ At vero eos et accusamus et iusto odio dignissimos ducimus qui blanditiis praesent ium voluptatum deleniti atque ”</p></div>
<div class="abs card" style="left:444px;top:2263px"><div class="mark">Kelmora</div><p>“ At vero eos et accusamus et iusto odio dignissimos ducimus qui blanditiis praesent ium voluptatum deleniti atque ”</p></div>
<div class="abs card" style="left:777px;top:2263px"><div class="mark">Fennwick</div><p>“ At vero eos et accusamus et iusto odio dignissimos ducimus qui blanditiis praesent ium voluptatum deleniti atque ”</p></div>

<div class="abs career" role="img" aria-label="Team meeting in an office under a green overlay"></div>
<h2 class="abs" style="left:110px;top:2688px;color:#fff;font-size:52px;font-family:Poppins,sans-serif;font-weight:500">Career</h2>
<p class="abs career-text">Nam libero tempore, cum soluta nobis est eligendi optio cumque nihil impedit quo minus id quod maxime placeat facere possimus, omnis voluptas assumenda est, omnis dolor repellend ibus autem quibusda.</p>
<div class="abs btn-more">VIEW MORE</div>
<div class="abs job" style="left:570px;top:2675px">
  <div class="pic" role="img" aria-label="Colleagues attending a presentation" style="background:linear-gradient(135deg,#cfd8e2,#6e7f92 60%,#3d4a5a)"></div>
  <h4>Finibus Bonoruet Malo</h4>
  <p>Nam libero tempore, cuisoluta nobis est eligendi optio cuque nihil impedit quo miq</p>
  <svg class="go" width="30" height="30" viewBox="0 0 30 30"><circle cx="15" cy="15" r="14" fill="#333" stroke="#fff" stroke-width="2"/><path d="M10 10 L15 15 L10 20 M15 10 L20 15 L15 20" fill="none" stroke="#fff" stroke-width="1.8"/></svg>
</div>
<div class="abs job" style="left:846px;top:2675px">
  <div class="pic" role="img" aria-label="Coworkers collaborating at a laptop" style="background:linear-gradient(135deg,#5a6d80,#a08a78 55%,#3b4756)"></div>
  <h4>Finibus Bonoruet Malo</h4>
  <p>Nam libero tempore, cuisoluta nobis est eligendi optio cuque nihil impedit quo miq</p>
  <svg class="go" width="30" height="30" viewBox="0 0 30 30"><circle cx="15" cy="15" r="14" fill="#333" stroke="#fff" stroke-width="2"/><path d="M10 10 L15 15 L10 20 M15 10 L20 15 L15 20" fill="none" stroke="#fff" stroke-width="1.8"/></svg>
</div>

<div class="abs contact" role="img" aria-label="Faded city skyline with a TV tower"></div>
<h2 class="abs section-title" style="top:3173px">Contact Us</h2>
<div class="abs col-title" style="left:110px;top:3290px">Contact form</div>
<div class="abs field" style="left:111px;top:3353px;width:297px;height:45px">Name :</div>
<div class="abs field" style="left:418px;top:3353px;width:296px;height:45px">Phone no :</div>
<div class="abs field" style="left:111px;top:3414px;width:603px;height:45px">Email :</div>
<div class="abs field" style="left:111px;top:3476px;width:603px;height:81px">Message :</div>
<div class="abs submit">SUBMIT</div>

<div class="abs col-title" style="left:778px;top:3290px">Contact Information</div>
<div class="abs info" style="top:3348px"><span class="ico"><svg width="12" height="16" viewBox="0 0 12 16"><path d="M6 15 C2 9 1 7 1 5.5 A5 5 0 0 1 11 5.5 C11 7 10 9 6 15Z" fill="#5aa52f"/><circle cx="6" cy="5.5" r="1.8" fill="#fff"/></svg></span><span>14 Lindenweg, Suite 3<br>80331 Musterstadt</span></div>
<div class="abs info" style="top:3414px"><span class="ico"><svg width="14" height="14" viewBox="0 0 14 14"><path d="M3 1 L5 4 L4 6 Q6 9 8 10 L10 9 L13 11 L11 13 Q5 13 1 3Z" fill="#5aa52f"/></svg></span><span style="padding-top:4px">+49 555 010 2040</span></div>
<div class="abs info" style="top:3474px"><span class="ico"><svg width="14" height="11" viewBox="0 0 14 11"><rect x="0.5" y="0.5" width="13" height="10" rx="1" fill="#5aa52f"/><path d="M1 1 L7 6 L13 1" fill="none" stroke="#fff" stroke-width="1.2"/></svg></span><span style="padding-top:4px">info@velmatrix.com</span></div>
<div class="abs col-title" style="left:778px;top:3548px">Social Media</div>
<div class="abs social"><span></span><span></span><span></span></div>

<div class="abs footer-line"></div>
<p class="abs copyright">Copyright © 2019, VelmaTrix. All rights reserved. Data protection &nbsp;|&nbsp; Imprint</p>
<svg class="abs" style="left:1063px;top:3710px" width="28" height="16" viewBox="0 0 28 16"><path d="M2 14 L14 3 L26 14" fill="none" stroke="#aaa" stroke-width="2.5"/></svg>

</body>
</html>
```